Murder Mystery Buffet Dinner Fundraiser. An Evening of Murder, Mystery & Mayhem

Camp fundraiser needs a 7-element promotional package. The elements are 1) a save the date post card, 2) a two-sided invitation, 3) an invitation envelope, 4) a rsvp card, 5) a rsvp envelope, 6) the front page of a playbill size program book and 7) a 8.5" x 11" flyer. We hope to attract 125 donors to attend a fundraising murder mystery buffet dinner to support a 70 + year old residential summer camp. We would like the elements in the package to be consist with one another. The package should have a consistent theme. The theme should be mysterious, but playful and engaging.

Target Market(s)

middle class, 25 to 70 year olds

Other font styles liked:
• Broadway Playbill style

Colors

Designer to choose colors to be used in the design.

Requirements
Must have
• A mysterious, fun off Broadway feeling
Nice to have
• Perhaps a shadowy mysterious figure(s) or 5 playing cards, 10, jack, queen , king, ace, either individually or collectively, representing something sinister
Should not have
• Anything above a pg rating

```html
<!DOCTYPE html>
<html lang="en">
<head>
<meta charset="utf-8">
<title>Hollis Murder Mystery Dinner</title>
<link rel="stylesheet" href="https://fonts.googleapis.com/css2?family=Barlow:wght@300;400;500;600;700&display=swap">
<style>
  :root {
    --ink: #010c14;
    --gold: #ffe234;
  }
  html, body {
    margin: 0;
    padding: 0;
    overflow: hidden;
    background: var(--ink);
  }
  .flyer {
    position: relative;
    width: 851px;
    height: 1200px;
    background: var(--ink);
    color: var(--gold);
    font-family: "Barlow", Arial, sans-serif;
    overflow: hidden;
  }
  .line {
    position: absolute;
    left: 0;
    width: 100%;
    text-align: center;
    line-height: 1;
    white-space: nowrap;
    margin: 0;
  }
  .tagline {
    font-size: 34px;
    font-weight: 500;
    letter-spacing: 0.4px;
  }
  .tagline-1 { top: 117px; }
  .tagline-2 { top: 155px; }

  .title-band {
    position: absolute;
    left: 0;
    top: 301px;
    width: 851px;
    height: 360px;
    background: var(--gold);
    color: var(--ink);
  }
  .title {
    font-size: 80px;
    font-weight: 700;
    letter-spacing: 9px;
    text-indent: 9px;
  }
  .title-1 { top: 86px; }
  .title-2 { top: 157px; }
  .subtitle {
    top: 262px;
    font-size: 27px;
    font-weight: 500;
    letter-spacing: 0;
  }

  .label {
    font-size: 38px;
    font-weight: 700;
  }
  .label .colon { font-weight: 400; margin-left: 10px; }
  .value {
    font-size: 31px;
    font-weight: 300;
    letter-spacing: 0;
  }
  .date-label { top: 727px; }
  .date-value { top: 778px; }
  .time-label { top: 849px; }
  .time-value { top: 903px; }
  .place-label { top: 981px; }
  .place-value-1 { top: 1036px; letter-spacing: 2.4px; }
  .place-value-2 { top: 1085px; letter-spacing: 1px; }
</style>
</head>
<body>
  <main class="flyer">
    <p class="line tagline tagline-1">JOIN US FOR AN EVENING OF</p>
    <p class="line tagline tagline-2">MYSTERY, MAYHEM AND MURDER!</p>

    <section class="title-band">
      <h1 class="line title title-1">HOLLIS MURDER</h1>
      <h1 class="line title title-2">MYSTERY DINNER</h1>
      <p class="line subtitle">A WAY OFF BROADWAY EVENING OF ENTERTAINMENT</p>
    </section>

    <p class="line label date-label">DATE<span class="colon">:</span></p>
    <p class="line value date-value">THURSDAY, OCTOBER 24, 2019</p>

    <p class="line label time-label">TIME<span class="colon">:</span></p>
    <p class="line value time-value">6 : 00 PM – 10 : 00 PM</p>

    <p class="line label place-label">LOCATION<span class="colon">:</span></p>
    <p class="line value place-value-1">LINDEN AVENUE COMMUNITY HALL</p>
    <p class="line value place-value-2">48 W 61ST ST, NEW YORK, NY 10023</p>
  </main>
</body>
</html>
```